RWT Fittings Ltd Business Cards

We need a business card with our business logo. We provide window and door installations on high-rises in west coast British Colombia, Canada.

I would like my business information and details on one side of the card, and the other side the company name with logo

Target Market(s)

General Contractors

Industry/Entity Type

Construction

Contact Information for Business Card

one side i want my company name and logo in the dark theme logo that i provided

Requirements
Must have
• Marco Peltieri, 16045518293, RWTFittings@mailbox-demo.com, 1407-5194 Linden Row Burnaby BC, V5H 2K9, Owner & Manager

```html
<!DOCTYPE html>
<html lang="en">
<head>
<meta charset="utf-8">
<title>RWT Fittings Ltd – Business Cards</title>
<link rel="stylesheet" href="https://fonts.googleapis.com/css2?family=Open+Sans:wght@400;600;700&display=swap">
<style>
  :root {
    --backdrop: #232323;
    --card: #1e1f23;
    --card-edge: #141518;
    --accent: #1e9ad6;
    --name-grey: #9a9a9c;
    --text: #f2f2f2;
    --logo-text: #c9cacc;
  }
  * { margin: 0; padding: 0; box-sizing: border-box; }
  html, body {
    width: 1200px; height: 780px; overflow: hidden;
    background: var(--backdrop);
    font-family: "Open Sans", Arial, sans-serif;
  }
  .sheet {
    position: relative; width: 1200px; height: 780px;
    display: flex; align-items: center; justify-content: center; gap: 60px;
  }
  .card {
    position: relative; width: 500px; height: 286px;
    background: var(--card);
    box-shadow: 0 3px 0 var(--card-edge), 0 6px 0 #18191c, 0 20px 40px rgba(0,0,0,.55);
    overflow: hidden;
  }
  /* Contact side */
  .card-front .fold-shadow {
    position: absolute; inset: 0;
    background: linear-gradient(115deg, transparent 50%, rgba(0,0,0,.32) 50.5%, rgba(0,0,0,0) 62%);
  }
  .person { position: absolute; left: 40px; top: 44px; }
  .person-name { font-size: 28px; font-weight: 700; letter-spacing: .2px; line-height: 1.1; }
  .person-name .first { color: var(--accent); }
  .person-name .last { color: var(--name-grey); }
  .person-role { margin-top: 4px; font-size: 14px; color: var(--text); }
  .contacts {
    position: absolute; left: 248px; top: 138px;
    list-style: none; font-size: 14px; color: var(--text); line-height: 1.75;
  }
  .contacts li { display: flex; align-items: center; gap: 8px; white-space: nowrap; }
  .contacts svg { width: 13px; height: 13px; fill: var(--accent); flex: none; }
  .address {
    position: absolute; left: 40px; bottom: 28px;
    font-size: 14px; color: var(--text); white-space: nowrap;
  }
  /* Company side */
  .card-back { display: flex; align-items: center; justify-content: center; }
  .brand { display: flex; align-items: center; gap: 14px; }
  .brand-mark { width: 34px; height: 34px; background: var(--accent); }
  .brand-name { font-size: 32px; font-weight: 700; color: var(--logo-text); letter-spacing: .5px; }
</style>
</head>
<body>
<main class="sheet">
  <section class="card card-front" aria-label="Business card, contact side">
    <div class="fold-shadow"></div>
    <div class="person">
      <p class="person-name"><span class="first">Marco</span> <span class="last">Peltieri</span></p>
      <p class="person-role">Owner &amp; Manager</p>
    </div>
    <ul class="contacts">
      <li><svg viewBox="0 0 24 24" aria-hidden="true"><path d="M6.6 10.8a15.1 15.1 0 0 0 6.6 6.6l2.2-2.2c.3-.3.7-.4 1-.2 1.1.4 2.3.6 3.6.6.6 0 1 .4 1 1V20c0 .6-.4 1-1 1A17 17 0 0 1 3 4c0-.6.4-1 1-1h3.5c.6 0 1 .4 1 1 0 1.3.2 2.5.6 3.6.1.3 0 .7-.2 1z"/></svg>(604) 551-8293</li>
      <li><svg viewBox="0 0 24 24" aria-hidden="true"><path d="M2 5h20v14H2zm2 2v.5l8 5 8-5V7zm0 2.8V17h16V9.8l-8 5z"/></svg>RWTFittings@mailbox-demo.com</li>
      <li><svg viewBox="0 0 24 24" aria-hidden="true"><path d="M12 2a10 10 0 1 0 0 20 10 10 0 0 0 0-20zm0 2c1 0 2.3 2 2.8 5H9.2C9.7 6 11 4 12 4zM4.3 11h3.7a18 18 0 0 0 0 2H4.3a8 8 0 0 1 0-2zm5.7 0h4a16 16 0 0 1 0 2h-4a16 16 0 0 1 0-2zm6 0h3.7a8 8 0 0 1 0 2H16a18 18 0 0 0 0-2zM9.2 15h5.6c-.5 3-1.8 5-2.8 5s-2.3-2-2.8-5z"/></svg>www.rwtfittings-demo.com</li>
    </ul>
    <p class="address">1407-5194 Linden Row Burnaby BC, V5H 2K9</p>
  </section>

  <section class="card card-back" aria-label="Business card, company side">
    <div class="brand">
      <span class="brand-mark" aria-hidden="true"></span>
      <span class="brand-name">RWT Fittings Ltd</span>
    </div>
  </section>
</main>
</body>
</html>
```